Restaurant Posters

Looking for two posters to be created for restaurant promos - see below for details:

Design #1 -
Want to highlight two main specials we offer - first is Tuesday BOGO Burgers (with purchase of two beverages), second is on Wednesday's we offer $0.75 Wings (includes traditional and boneless) and $2 off IPA's

Then at the bottom smaller would like to call out two less important offers - first is $2 off Nebraska Beers on Mondays, and the second is 1/2 off 19.2oz Crowlers on Thursdays

Design #2 -
Looking to create a sign up for our e-club and receive a free appetizer upon sign up, free burger on your birthday week, and access to exclusive deals and email offers

See attached for supporting docs you may use - don't have to but feel free to get creative with these. Would like the designs to be simple, and follow our brand look and feel as much as possible. Our website is not a good indication of our brand - I would go more off of our logos, and our menu design.

```html
<!DOCTYPE html>
<html lang="en">
<head>
<meta charset="utf-8">
<title>Ridgeline Tap House – Weekly Specials</title>
<link rel="stylesheet" href="https://fonts.googleapis.com/css2?family=Bodoni+Moda:wght@700;900&family=Oswald:wght@500;700&family=Roboto+Slab:wght@500;700&family=Courier+Prime:wght@400;700&display=swap">
<style>
  :root {
    --brand-red: #e0161c;
    --deep-red: #c40f14;
    --ink: #111111;
    --paper: #ffffff;
    --sun: #ffe300;
    --rule: #9a9a9a;
  }
  * { margin: 0; padding: 0; box-sizing: border-box; }
  html, body { width: 849px; height: 1200px; overflow: hidden; background: var(--paper); }
  .poster {
    position: relative;
    width: 849px;
    height: 1200px;
    overflow: hidden;
    background: var(--brand-red);
    font-family: "Courier Prime", monospace;
    color: var(--ink);
  }
  .poster > * { position: absolute; }

  .shapes { left: 0; top: 0; width: 849px; height: 976px; }

  .brand {
    left: 92px; top: 62px;
    display: flex; align-items: center; gap: 12px;
    font-family: "Oswald", sans-serif; font-weight: 700;
    font-size: 30px; line-height: 1; letter-spacing: 2px;
    color: var(--ink); text-transform: uppercase;
  }
  .brand-mark { width: 22px; height: 22px; background: var(--ink); }

  .headline-top {
    left: 330px; top: 84px; width: 500px;
    font-family: "Bodoni Moda", serif; font-weight: 900;
    font-size: 78px; line-height: 1; text-align: center; white-space: nowrap;
    transform: scaleX(0.76); transform-origin: center;
    letter-spacing: 2px;
  }
  .headline-main {
    left: -100px; top: 150px; width: 1156px;
    font-family: "Bodoni Moda", serif; font-weight: 900;
    font-size: 220px; line-height: 1; text-align: center; white-space: nowrap;
    transform: scaleX(0.7); transform-origin: center;
    letter-spacing: 4px;
  }

  .day-tag {
    font-family: "Roboto Slab", serif; font-weight: 700;
    font-size: 21px; letter-spacing: 2px; line-height: 1;
    padding: 5px 0 4px;
    border-top: 3px solid currentColor;
    border-bottom: 3px solid currentColor;
    text-transform: uppercase;
  }

  .burger-offer { left: 50px; top: 404px; }
  .burger-offer .day-tag { color: var(--deep-red); display: inline-block; }
  .burger-title { margin-top: 10px; line-height: 0.95; }
  .burger-title .accent {
    font-family: "Oswald", sans-serif; font-weight: 500;
    font-size: 78px; color: var(--brand-red); letter-spacing: 1px;
  }
  .burger-title .word {
    font-family: "Roboto Slab", serif; font-weight: 500;
    font-size: 44px; letter-spacing: 2px; text-transform: uppercase;
  }
  .offer-note { font-size: 22px; line-height: 1.1; margin-top: 4px; }

  .photo-burger {
    left: 100px; top: 641px; width: 342px; height: 335px;
    border-radius: 48% 48% 30% 30%;
    background: radial-gradient(ellipse at 50% 45%, #f3ead2 0%, #d9973f 45%, #8a4a1e 100%);
  }
  .photo-wings {
    left: 412px; top: 365px; width: 428px; height: 300px;
    border-radius: 50%;
    background: radial-gradient(ellipse at 45% 45%, #f2b04a 0%, #d97a1f 55%, #a5521a 100%);
  }

  .wings-offer { left: 490px; top: 690px; width: 340px; }
  .wings-offer .day-tag {
    display: inline-block; color: var(--ink);
    border-top: none; padding-left: 6px; padding-right: 10px;
  }
  .wings-price { margin-top: 8px; white-space: nowrap; line-height: 1; margin-left: 20px; }
  .wings-price .amount {
    font-family: "Oswald", sans-serif; font-weight: 500;
    font-size: 68px; color: var(--brand-red);
  }
  .wings-price .amount sup { font-size: 34px; vertical-align: 26px; }
  .wings-price .word {
    font-family: "Roboto Slab", serif; font-weight: 500;
    font-size: 42px; letter-spacing: 1px; margin-left: 6px;
  }
  .wings-offer .offer-note { font-size: 21px; margin-top: 6px; margin-left: 16px; }

  .ipa-badge {
    left: 688px; top: 833px; width: 114px; height: 114px;
    border-radius: 50%; background: var(--sun);
    display: flex; flex-direction: column; align-items: center; justify-content: center;
    font-family: "Roboto Slab", serif; font-weight: 700; color: var(--brand-red);
    line-height: 0.95; transform: rotate(-10deg);
  }
  .ipa-badge .lead { font-family: "Oswald", sans-serif; font-size: 42px; }
  .ipa-badge .lead small { font-size: 18px; }
  .ipa-badge .tail { font-size: 28px; }

  .minor-offers {
    left: 0; top: 976px; width: 849px; height: 224px;
    background: var(--paper); border-top: 3px solid var(--rule);
    display: flex;
  }
  .minor-offer { position: relative; flex: 1; overflow: hidden; }
  .minor-offer + .minor-offer { border-left: 2px solid var(--rule); }
  .minor-offer .ribbon { position: absolute; left: 28px; top: 7px; width: 100px; height: 200px; }
  .minor-offer .ribbon-text {
    position: absolute; left: 28px; top: 22px; width: 100px;
    text-align: center; color: var(--paper);
    font-family: "Oswald", sans-serif; font-weight: 700; line-height: 1;
  }
  .ribbon-text .day-tag {
    display: inline-block; background: var(--sun); color: var(--deep-red);
    font-size: 15px; padding: 3px 4px; letter-spacing: 0;
    border-width: 2px;
  }
  .ribbon-text .value { font-size: 62px; margin-top: 8px; }
  .ribbon-text .value.fraction { font-size: 64px; }
  .ribbon-text .off { font-size: 30px; margin-top: 2px; }
  .minor-title {
    position: absolute; left: 142px; top: 26px;
    font-family: "Roboto Slab", serif; font-weight: 500;
    font-size: 30px; line-height: 1.05; white-space: nowrap;
  }
  .minor-offer .spot {
    position: absolute; left: 262px; top: 116px; width: 152px; height: 152px;
    border-radius: 50%; background: var(--brand-red);
  }
  .minor-offer .can {
    position: absolute; left: 296px; top: 62px; width: 84px; height: 150px;
    border-radius: 10px;
  }
  .can-beer { background: linear-gradient(90deg, #2b5d4a, #9cc08a 50%, #2b5d4a); }
  .can-crowler { background: linear-gradient(90deg, #9a9ea3, #f1f2f3 50%, #9a9ea3); }
</style>
</head>
<body>
<main class="poster">
  <svg class="shapes" viewBox="0 0 849 976" aria-hidden="true">
    <circle cx="214" cy="690" r="335" fill="#ffffff"/>
    <circle cx="690" cy="712" r="260" fill="#ffffff"/>
  </svg>

  <div class="brand"><span class="brand-mark"></span>Ridgeline Tap House</div>

  <h1 class="headline-top">SPECIALS</h1>
  <div class="headline-main">OFFER</div>

  <div class="photo-wings" role="img" aria-label="Photo of crispy fried chicken wings"></div>
  <div class="photo-burger" role="img" aria-label="Photo of a loaded cheeseburger topped with fried chicken"></div>

  <section class="burger-offer">
    <div class="day-tag">Tuesday</div>
    <h2 class="burger-title">
      <span class="accent">FREE</span> <span class="word">Bogo</span><br>
      <span class="word">Burgers</span>
    </h2>
    <p class="offer-note">with purchase of<br>two beverages</p>
  </section>

  <section class="wings-offer">
    <div class="day-tag">All Day</div>
    <h2 class="wings-price"><span class="amount"><sup>$</sup>0.75</span><span class="word">WINGS</span></h2>
    <p class="offer-note">(includes traditional<br>&amp; boneless)</p>
  </section>

  <div class="ipa-badge"><span class="lead">$2<small>OFF</small></span><span class="tail">IPA's</span></div>

  <section class="minor-offers">
    <article class="minor-offer">
      <svg class="ribbon" viewBox="0 0 100 200" aria-hidden="true"><path d="M0 0H100V200L50 174L0 200Z" fill="#e0161c"/></svg>
      <div class="ribbon-text">
        <span class="day-tag">Monday</span>
        <div class="value">$2</div>
        <div class="off">OFF</div>
      </div>
      <h3 class="minor-title">Nebraska<br>Beers</h3>
      <div class="spot"></div>
      <div class="can can-beer" role="img" aria-label="Photo of a can of local beer"></div>
    </article>
    <article class="minor-offer">
      <svg class="ribbon" viewBox="0 0 100 200" aria-hidden="true"><path d="M0 0H100V200L50 174L0 200Z" fill="#e0161c"/></svg>
      <div class="ribbon-text">
        <span class="day-tag">Thursday</span>
        <div class="value fraction">½</div>
        <div class="off">OFF</div>
      </div>
      <h3 class="minor-title">19.2oz<br>Crowlers</h3>
      <div class="spot"></div>
      <div class="can can-crowler" role="img" aria-label="Photo of a silver crowler can"></div>
    </article>
  </section>
</main>
</body>
</html>
```